Creative, fresh business card design for Ripplecraft Facades

We need a fresh, creative business card design for Ripplecraft Facades. We are the manufacturer of Ripplecraft Facades in Australia. Wall panels are 2400 x 1200mm panels made from MDF and feature 3D patterns on the face of the panel. The colours to be used are green, silver/grey and white RGB
Red 187
Green 207
Blue 65.

An idea is to possibly use a watermark of one of our designs as a background (like on the "Grids" design on the left hand side of page 2 of our brochure).

Target Market(s)

Interior designers, architects, builders and home renovators

Industry/Entity Type

Business

Contact Information for Business Card

Details to go on the card are:
Our logo (attached),
Slogan: "Decorative panels for interiors and exteriors",
Contact name,
Position,
Mobile phone number,
Business address,
Business phone,
Business fax,
Website and
Email address.

I have attached a few images of our panels and our brochure for reference.

The colours of the business card should feature our logo colours which are: RGB
Red 187
Green 207
Blue 65

Requirements
Must have
• Very modern fonts and design. Some of the designs shown especially the "Prisms" design which is a popular design.
Nice to have
• Creative but simple design. Very contemporary.
Should not have
• Anything ornate or old fashioned.

```html
<!DOCTYPE html>
<html lang="en">
<head>
<meta charset="utf-8">
<title>Ripplecraft Facades – Business Card</title>
<link rel="stylesheet" href="https://fonts.googleapis.com/css2?family=Arimo:wght@400;700&family=Open+Sans:wght@400&family=Roboto:wght@300&display=swap">
<style>
  :root {
    --brand-green: #bbcf41;
    --brand-green-deep: #8a9a1c;
    --ink: #2b2b2b;
    --band-dark: #2a2a28;
    --band-grey: #8c8a86;
    --band-grey-text: #ecebe8;
    --card-face: #f4f2ee;
    --card-edge: #dcd8d0;
    --backdrop: #e4ddd2;
    --body-text: #3a3a3a;
  }
  * { margin: 0; padding: 0; box-sizing: border-box; }
  html, body {
    width: 1200px; height: 1000px; overflow: hidden;
    background: var(--backdrop);
  }
  .canvas { position: relative; width: 1200px; height: 1000px; }
  .card {
    position: absolute; left: 405px; top: 85px;
    width: 430px; height: 790px;
    background: var(--card-face);
    border: 1px solid var(--card-edge);
    border-radius: 18px;
    overflow: hidden;
    box-shadow: 0 10px 30px rgba(80, 70, 50, 0.15);
  }
  .brand-band {
    height: 185px; background: var(--brand-green);
    display: flex; flex-direction: column; justify-content: center;
    padding: 0 22px;
  }
  .brand-name {
    font-family: "Arimo", Arial, sans-serif; font-weight: 700;
    font-size: 58px; line-height: 0.98; color: var(--band-dark);
    letter-spacing: -1px;
  }
  .divider { height: 12px; background: var(--band-dark); }
  .title-band {
    height: 63px; background: var(--band-grey);
    display: flex; align-items: center; justify-content: center;
  }
  .company-title {
    font-family: "Roboto", Arial, sans-serif; font-weight: 300;
    font-size: 37px; color: var(--band-grey-text); letter-spacing: -0.5px;
  }
  .slogan-band {
    height: 68px; background: var(--band-dark);
    display: flex; flex-direction: column; justify-content: center; align-items: center;
    font-family: "Open Sans", Arial, sans-serif; font-size: 17px;
    color: var(--brand-green); letter-spacing: 6.3px; line-height: 31px;
  }
  .contact-block { position: absolute; left: 44px; top: 398px; }
  .person-name {
    font-family: "Arimo", Arial, sans-serif; font-weight: 700;
    font-size: 34px; color: var(--ink); line-height: 1;
  }
  .person-name .surname { color: var(--brand-green-deep); }
  .person-role {
    font-family: "Open Sans", Arial, sans-serif; font-size: 22px;
    color: var(--body-text); margin-top: 4px;
  }
  .address {
    font-family: "Open Sans", Arial, sans-serif; font-size: 18px;
    color: var(--body-text); line-height: 24px; margin-top: 22px;
  }
  .details { list-style: none; margin-top: 18px; }
  .details li {
    display: flex; align-items: center; height: 28.5px;
    font-family: "Open Sans", Arial, sans-serif; font-size: 20px; color: var(--body-text);
  }
  .details svg { width: 16px; height: 16px; margin-right: 18px; flex: none; fill: var(--brand-green-deep); }
</style>
</head>
<body>
<main class="canvas">
  <article class="card">
    <header class="brand-band">
      <div class="brand-name">Ripplecraft<br>Facades</div>
    </header>
    <div class="divider"></div>
    <div class="title-band"><span class="company-title">Ripplecraft Facades</span></div>
    <div class="slogan-band">
      <span>Decorative Panels for</span>
      <span>interiors and exteriors</span>
    </div>

    <section class="contact-block">
      <h1 class="person-name">Aldo <span class="surname">Brennan</span></h1>
      <p class="person-role">Director</p>
      <p class="address">14 Harbour Lane,<br>Sydney, 2000</p>
      <ul class="details">
        <li>
          <svg viewBox="0 0 16 16" aria-hidden="true"><path d="M4 0h8a1 1 0 0 1 1 1v14a1 1 0 0 1-1 1H4a1 1 0 0 1-1-1V1a1 1 0 0 1 1-1zm1 2v10h6V2zm3 11a1 1 0 1 0 0 2 1 1 0 0 0 0-2z"/></svg>
          +61 400 555 012
        </li>
        <li>
          <svg viewBox="0 0 16 16" aria-hidden="true"><path d="M3.6 1 6 3.6 4.7 5.4c.9 2 2.6 3.8 4.6 4.7L11 8.8 13.6 11 12.4 13.8C6.8 13.8 1.6 8.6 1.6 3z"/></svg>
          +61 2 5550 1234
        </li>
        <li>
          <svg viewBox="0 0 16 16" aria-hidden="true"><path d="M4 1h6l2 2v3H4zM1 7h14v7H1zm9 2v1.5h3V9zm0 2.5V13h3v-1.5zM3 9v4h5V9z"/></svg>
          +61 2 5550 1235
        </li>
        <li>
          <svg viewBox="0 0 16 16" aria-hidden="true"><path d="M1 3h14v10H1zm1.5 1.2v.6L8 9l5.5-4.2v-.6z"/></svg>
          aldo@ripplecraft.example
        </li>
        <li>
          <svg viewBox="0 0 16 16" aria-hidden="true"><path d="M9.5 1a5.5 5.5 0 1 1-3.3 9.9L2.4 14.7 1.3 13.6l3.8-3.8A5.5 5.5 0 0 1 9.5 1zm0 2a3.5 3.5 0 1 0 0 7 3.5 3.5 0 0 0 0-7z"/></svg>
          www.ripplecraft.example
        </li>
      </ul>
    </section>
  </article>
</main>
</body>
</html>
```